Product labels for new supplements business targeting high performing creative people

I need a label design for different supplements like Whey, BCAA, Melatonin etc. that I could customize for each use case separately.

The brand is called moonquell.life, and it would be the first design of the labels. We haven't sold any products yet, but the target audience is people with growth mindset, people who want to be as efficient as possible and are constantly looking to improve their lifestyle. As part of that, they are also working out, but don't know much about supplements yet. Mostly people between 20-34.

I don't have a too specific idea of the expected design, though it should be light, warm, smart and minimalist, maybe have some patterns. It should looks smart and clean (and expensive). Orange and golden might be the additional colors for white. I have attached the templates of some products that I plan to sell and also the logo of the brand.

Here's what I have used for inspiration:
Brands that I like and are somewhat similar in concept: https://www.vantrel.com/ (!!specially the way they
bring "how the product helps them" in focus, not "what the product is" & https://www.plomi.care/ &
https://www.delvora.com/sport/ & https://en.kalobrine.fr/ &
https://48sketchworks.com/profiles/marenhollowaydesign/designs/617482

Here's how different products look like: https://grenvolt.com/catalog

Target Market(s)

target audience is people with growth mindset, people who want to be as efficient as possible and are constantly looking to improve their lifestyle. As part of that, they are also working out, but don't know much about supplements yet. Mostly people between 20-34.

Industry/Entity Type

Supplements

Font styles to use
Sans Serif

Colors
FFC000
F8CF3A
FAE287
FDF2CF
FEFAEE
F0912C
F2A743
F7CA91
FBE8D2
FDF5EE
EE7325
F08F49
F5BC92
FAE3D3
FDF4ED

Requirements
Must have
• Clean, smart and minimalist design that can be applied for different products in different sizes, like Whey protein, BCAA, vitamins etc. available here: https://grenvolt.com/catalog
Nice to have
• Patterns, expensive look
Should not have
• Doodles, too many colors

```html
<!DOCTYPE html>
<html lang="en">
<head>
<meta charset="utf-8">
<title>moonquell.life — Melatonin label</title>
<link rel="stylesheet" href="https://fonts.googleapis.com/css2?family=Anton&family=Roboto+Condensed:wght@400;500&display=swap">
<style>
  :root {
    --page: #f4f4f4;
    --label-yellow: #fcd93e;
    --band-orange: #f7b23c;
    --band-edge: #f5a52f;
    --diamond: #f9c933;
    --ink: #1c1a17;
  }
  html, body {
    margin: 0;
    width: 1200px;
    height: 1200px;
    overflow: hidden;
    background: var(--page);
  }
  .label {
    position: absolute;
    left: 190px;
    top: 100px;
    width: 820px;
    height: 1000px;
    background: var(--label-yellow);
    overflow: hidden;
    font-family: "Roboto Condensed", sans-serif;
    color: var(--ink);
  }
  .band {
    position: absolute;
    left: 0;
    width: 100%;
    background: var(--band-orange);
  }
  .band--top { top: 0; height: 70px; border-bottom: 6px solid var(--band-edge); }
  .band--bottom { bottom: 0; height: 127px; border-top: 6px solid var(--band-edge); }
  .pattern-field {
    position: absolute;
    inset: 0;
  }
  .diamond {
    position: absolute;
    left: 0;
    top: 0;
  }
  .brand {
    position: absolute;
    top: 238px;
    left: 0;
    width: 100%;
    display: flex;
    justify-content: center;
    align-items: center;
    gap: 20px;
  }
  .brand__mark {
    width: 54px;
    height: 54px;
    border-radius: 50%;
    background: var(--band-edge);
  }
  .brand__name {
    font-weight: 500;
    font-size: 80px;
    line-height: 1;
    letter-spacing: 1px;
  }
  .product {
    position: absolute;
    left: 0;
    width: 100%;
    text-align: center;
    margin: 0;
  }
  .product__name {
    top: 500px;
    font-family: "Anton", sans-serif;
    font-weight: 400;
    font-size: 112px;
    line-height: 1;
    letter-spacing: -2px;
  }
  .product__dose {
    top: 625px;
    font-size: 56px;
    font-weight: 400;
    line-height: 1;
  }
  .benefits {
    top: 710px;
    font-size: 36px;
    line-height: 52px;
  }
  .meta {
    position: absolute;
    top: 832px;
    font-size: 30px;
    text-transform: none;
  }
  .meta--left { left: 8px; text-transform: uppercase; }
  .meta--right { right: 18px; }
</style>
</head>
<body>
  <section class="label">
    <div class="pattern-field" role="img" aria-label="Fine repeating scallop pattern in warm yellow across the label"></div>
    <div class="band band--top"></div>
    <div class="band band--bottom"></div>

    <svg class="diamond" width="820" height="1000" viewBox="0 0 820 1000" aria-hidden="true">
      <path d="M410 130 Q430 130 445 150 L765 470 Q785 490 765 510 L445 830 Q430 850 410 850 Q390 850 375 830 L55 510 Q35 490 55 470 L375 150 Q390 130 410 130 Z" fill="var(--diamond)"/>
    </svg>

    <div class="brand">
      <span class="brand__mark"></span>
      <span class="brand__name">moonquell.life</span>
    </div>

    <h1 class="product product__name">MELATONIN</h1>
    <p class="product product__dose">1 mg</p>
    <p class="product benefits">Fall asleep faster*<br>Stay asleep longer*</p>

    <span class="meta meta--left">Dietary Supplement</span>
    <span class="meta meta--right">60 tablets</span>
  </section>
</body>
</html>
```